Velmora Gems - High end custom Jewelry website

I need a web design for an online custom jewelry company called Velmora Gems. (www.velmoragems-demo.com) this company specializes in high-end custom made engagement rings, wedding bands and jewelry of all kinds (necklaces, earrings, bracelets etc)All our jewelry uses diamonds so there must be a focus on diamonds on every type of jewelry we will be designing off the website.

We are a company located in New York City but our website will
aim to cater to international, national clients and as well as New York city residents.The company low overhead provides diamonds and precious metal at a discounted costs compared to its competitors. Velmora Gems makes unique custom diamond jewelry of a higher quality and at a lower price than carriage trade retail jewellers. (meaning that our company allows our customers to save money on diamond jewelry then they would if they bought from any known store or company)

The website will act as a tool for our customers to create their own jewelry. The way they will do this is by uploading pictures of what they like, they can post any pictures they want (from drawings, to actual copy and pasted pictures from other websites of designs) From these designs we will create a 3D digital image of the jewelry they like and customize it - however they want (colours, size etc) and then give them a quote in price. From the quote they will either approve it and we can have it made for them in 1 weeks time. If they decline it we will try to do whatever it is they want for the design to suit their needs.

We want the website to be simple and user friendly since people will be working on it to create their own individual jewelry pieces. Therefore some useful headings should include:

"Custom Jewellery" or something like "your design" "Custom Design"

a drop heading here should show the following steps into creating the jewelry.

step 1:
upload pictures of the designs you like
step 2:
What is your ring size?
Step 3:
What setting would you like your ring in? platinum, 14k etc..
Step 4:
What is your budget?
Step 5 :
Once you’ve uploaded pictures and give an explanation of what you want then we will contact you by phone or email and proceed to design your ring. Give us your contact info in this step.

Other then that other headings id like to see on the site are:

"Home"
main page with appealing picture which I can later add text to it explaining our company

"About us"
will include a brief section of who we are

"Wedding/engagment"

We are based in New York City and our company offers a one-to-one personal service to our clients ensuring their expectations are well met and, if we can help it, surpassed. We are a personal shopping and diamond supplier to individuals. Custom design is our speciality weather it be wedding ring, engagement ring or anniversary ring we aim to create distinctive designs that both reflect your personality as well as the beauty of the gemstones used in your piece. We use platinum, 14l-18k gold and diamonds to whatever it is that you may desire.
We in our company believe that we are privileged to be a part of one of the biggest events in our customer’s lives, and we pride ourselves on making sure that our customers have the best experience possible. As the diamond is the center piece of every engagement ring, we at VG make sure that our clients find the best diamond possible that is within their budget. Similarly, we work with established jewellery artisans from Belgium to provide the highest possible craftsmanship to a ring design of your choice. We make sure that our rings are made by the true and tried traditional methods focused on quality rather than quantity and of course our diamonds are QRB certified.

Diamonds

A section that explains where our diamonds come from. A heading will drop down here that is a diamond guide, as shown below.
Diamond Guide

An overview of the 4 C’s and different settings, a section for a brief education on diamonds.
Client Experiences

A section where clients share their experiences with Velmora Gems and can post pictures and share stories about their engagement etc.

The colour i would like to see are white and black, white and dark blue or royal blue. I don't think pastel colours will look good with this, maybe accents of purple or something pastel but for the main colours I want to keep it classic and sophisticated since it is a diamond company.

"Sign in | Check out"
where users are able to create a profile and upload their pictures and create their designs..

and a "search section"

or something along these lines or if you can incorporate both:

Exquisite craftsmanship Finest quality diamonds
Will beat any competitors price by twenty to seventy percent guaranteed
Price quotes whitin24 hours

Upload design picture or sketch
Receive price quote within 24hours
Receive and approve free customized design
Receive you jewelry in 1 week or less

Engagment Ring or necklace, earring, etc
Name
EMail
phone
Competitior Link
Budget

The final design should communicate that Velmora Gems is a custom jewelry site that allows individuals to personalize any type of jewellery they want with diamonds - at a fraction of the cost in comparison to any other out there. Our team works very hard to ensure that you will be so involved in the custom order process that there is no chance of something not being made to your requests. Jewelry is made to the highest standard or it does not ship in the first place. In the event a custom order does not suit a customer, we will take returns within 14 days of delivery less a 25% restocking fee.

Target Market(s)

middle class and upper class people ages 25-45

Industry/Entity Type

Digital

Requirements
Must have
• We have the logo now that I will attach BUT if you want to design something else please feel free ! I am open to all designs and ideas.
My logo now is simply a sketch so even if we make it look a bit more professional and classy I would like that, I think I want to keep it simple just black and white and maybe make the diamond shiny if possible. other then black in white I liked the gold and black combination too.. but as I said open to any other creative ideas!

can take pictures of jewelry off this website:
http://www.plinthwaredesigns.example/library/rings.html
Nice to have
• We already have a logo but we would like to see a banner or something that indicated saving money on diamond jewelry without it looking tacky or too cheap..

Also would like to see artistic pictures if you can of jewelry alongside very simple designs of jewelry that the masses like, (anything trendy or appealing to the eye)

cursive or elegant writing could be nice, flash could also be incorporated in the main page..

Should not have
• Nothing to old fashioned, when I mean elegant maybe just the the name of the company in cursive writing (Velmora Gems) but the actual headings and font on the website to be in a widely used font on jewelry websites. Please no hot pink colours or anything neon..
no times new roman font..

```html
<!DOCTYPE html>
<html lang="en">
<head>
<meta charset="utf-8">
<title>Velmora Gems – Custom Diamond Jewellery</title>
<link href="https://fonts.googleapis.com/css2?family=Cinzel:wght@400&family=Raleway:wght@200;300&family=Roboto+Condensed:wght@400;700&family=PT+Sans+Narrow:wght@400;700&family=Oswald:wght@400;500&family=Cabin:wght@400&family=Open+Sans:wght@400;600&family=Great+Vibes&display=swap" rel="stylesheet">
<style>
:root{
  --page-bg:#1c1c1c;
  --page-bg-deep:#111;
  --panel:#2a2a2a;
  --text-light:#e8e8e8;
  --text-muted:#a9a9a9;
  --text-dim:#8a8a8a;
  --gold:#f3c97a;
  --gold-deep:#b48a3f;
  --blue:#2f7fc9;
  --red:#e0261d;
  --field-border:#5a5a5a;
}
*{box-sizing:border-box;margin:0;padding:0}
html,body{width:975px;height:1200px;overflow:hidden;background:var(--page-bg-deep)}
.canvas{position:relative;width:975px;height:1200px;overflow:hidden;
  background:radial-gradient(ellipse at 50% 40%,#2b2b2b 0%,var(--page-bg) 55%,var(--page-bg-deep) 100%);
  font-family:"Open Sans",sans-serif;color:var(--text-light)}
.abs{position:absolute}

/* header */
.brand{left:97px;top:22px;display:flex;align-items:center;gap:10px}
.brand-dot{width:46px;height:46px;border-radius:50%;background:#f2f2f2}
.brand-name{font-family:"Great Vibes",cursive;font-size:30px;color:#f2f2f2;line-height:1}
.account-links{left:770px;top:48px;font-family:"Open Sans",sans-serif;font-size:7.5px;color:var(--text-muted);letter-spacing:.3px;word-spacing:2px}
.search{left:489px;top:68px;width:246px;height:18px;display:flex;border:1px solid #999}
.search-input{flex:1;background:#fff;color:#777;font-size:8.5px;padding:3px 7px;font-family:"Open Sans",sans-serif}
.search-btn{width:42px;background:linear-gradient(#777,#555);color:#eee;font-size:7px;text-align:center;line-height:16px}
.cart{left:750px;top:67px;width:128px;height:20px;background:#fff;font-size:7.5px;color:#666;text-align:center;line-height:20px}
.cart b{color:var(--red);font-weight:400}

/* navigation */
.nav{left:97px;top:114px;width:781px;height:35px;background:linear-gradient(#4a4a4a,#2a2a2a 55%,#1e1e1e);border-radius:3px 3px 0 0}
.nav a{position:absolute;top:11px;font-family:"Roboto Condensed",sans-serif;font-weight:700;font-size:9px;color:#e6e6e6;text-decoration:none}

/* hero */
.hero{left:97px;top:155px;width:781px;height:345px;background:radial-gradient(ellipse at 60% 35%,#8e8e8e 0%,#4a4a4a 35%,#1a1a1a 75%,#0c0c0c 100%)}
.hero-art{position:absolute;left:317px;top:32px;width:390px;height:313px;border-radius:160px 160px 20px 20px;background:radial-gradient(ellipse at 50% 40%,#e6e6e6 0%,#a8a8a8 40%,rgba(80,80,80,.2) 80%,transparent 100%)}
.hero-title{position:absolute;left:54px;top:48px;font-family:"Cinzel",serif;font-size:36px;line-height:44px;color:#fff}
.hero-offer{position:absolute;left:58px;top:137px;font-family:"Raleway",sans-serif;font-weight:200;font-size:52px;color:var(--gold);line-height:1}
.hero-sub{position:absolute;left:54px;top:210px;font-family:"Cinzel",serif;font-size:18px;color:#fff}
.hero-btn{position:absolute;left:58px;top:252px;width:163px;height:38px;background:linear-gradient(#f4f4f4,#a9a9a9);border-radius:2px;font-family:"Cinzel",serif;font-size:16px;color:#666;text-align:center;line-height:38px}
.hero-dots{position:absolute;left:734px;top:326px;display:flex;gap:3px}
.hero-dots span{width:7px;height:7px;background:#666}

/* welcome */
.welcome{left:97px;top:520px;width:781px;text-align:center}
.welcome h1{font-family:"PT Sans Narrow",sans-serif;font-weight:400;font-size:25px;color:#fff}
.welcome p{margin-top:8px;font-family:"PT Sans Narrow",sans-serif;font-size:9.3px;line-height:17px;color:var(--text-muted);text-transform:uppercase;letter-spacing:-.1px}

/* promo tiles */
.tile{width:385px;height:132px;overflow:hidden}
.tile-art{position:absolute}
.tile-bracelets{left:97px;top:608px;background:linear-gradient(110deg,#eef4fa 0%,#a9cde9 45%,#3f8ad0 100%)}
.tile-offer{left:493px;top:608px;background:linear-gradient(90deg,#9a7534 0%,#c69e55 50%,#a98242 100%)}
.tile-stones{left:97px;top:751px;background:#050505}
.tile-dollars{left:493px;top:751px;background:#fff;border:2px solid #ddd}
.cond{font-family:"Oswald",sans-serif;position:absolute;white-space:nowrap}
.tile-bracelets .l1{left:179px;top:20px;font-size:24px;color:var(--blue)}
.tile-bracelets .l2{left:179px;top:56px;font-size:16.5px;color:#111}
.tile-bracelets .l3{left:179px;top:80px;font-size:20px;color:var(--red)}
.tile-offer .l1{left:45px;top:30px;font-size:16px;color:#111}
.tile-offer .l2{left:69px;top:50px;font-size:24px;color:#ffd21a;font-weight:500}
.tile-offer .l3{left:53px;top:84px;font-size:16px;color:#111}
.tile-stones .l1{position:absolute;left:225px;top:6px;font-family:"Cabin",sans-serif;font-size:21px;color:#fff}
.tile-stones .l2{position:absolute;left:256px;top:24px;font-family:"Cabin",sans-serif;font-size:32px;color:#fff}
.tile-stones .l3{position:absolute;left:252px;top:78px;font-family:"Raleway",sans-serif;font-weight:300;font-size:13px;color:var(--gold)}
.tile-stones .l4{position:absolute;left:252px;top:98px;font-family:"Raleway",sans-serif;font-weight:300;font-size:26px;color:var(--gold)}
.tile-dollars .l1{position:absolute;left:36px;top:12px;font-family:"Open Sans",sans-serif;font-size:23px;color:#111}
.tile-dollars .l2{left:22px;top:50px;font-size:20px;color:var(--red);font-weight:500}
.tile-dollars .rule{position:absolute;left:22px;width:207px;height:3px;border-top:1px solid #ccc;border-bottom:1px solid #ccc}
.tile-dollars .l3{left:47px;top:82px;font-size:16px;color:#888}

/* quotes */
.promise{left:97px;top:910px;width:781px;text-align:center;font-family:"PT Sans Narrow",sans-serif;font-size:17.5px;line-height:27px;color:var(--text-muted)}

/* footer */
.footer{left:97px;top:1006px;width:781px;height:146px;background:var(--panel)}
.footer-links{position:absolute;left:31px;top:14px;list-style:none;font-size:8.5px;line-height:17px;color:#d4d4d4}
.enquiry-title{position:absolute;left:166px;top:16px;font-size:14px;color:#f0f0f0}
.field{position:absolute;width:150px;height:19px;border:1px solid var(--field-border);font-size:7.5px;color:#9a9a9a;padding:4px 10px}
.submit{position:absolute;left:324px;top:107px;width:66px;height:18px;background:linear-gradient(#fff,#bbb);border-radius:2px;font-size:7.5px;color:#333;text-align:center;line-height:18px}
.badge{position:absolute;left:507px;top:26px;width:252px;height:60px}
.badge-band{position:absolute;left:38px;top:0;width:214px;height:60px;border-radius:3px;background:linear-gradient(90deg,#7d5a25,#c7a061 40%,#e0bf80)}
.badge-globe{position:absolute;left:0;top:-4px;width:66px;height:66px;border-radius:50%;background:radial-gradient(circle at 40% 35%,#fff5d9,#d8b46a 55%,#8e6a2c)}
.badge-title{position:absolute;left:79px;top:9px;font-size:16px;color:#fff}
.badge-sub{position:absolute;left:79px;top:33px;font-size:11.5px;color:#1a1a1a}
.follow{position:absolute;left:618px;top:112px;font-size:7.5px;color:#aaa;letter-spacing:.3px}
.social{position:absolute;top:106px;width:24px;height:24px;border-radius:50%}
.copyright{left:97px;top:1163px;width:781px;text-align:center;font-size:8px;color:#9a9a9a}
</style>
</head>
<body>
<div class="canvas">

  <header>
    <div class="abs brand"><span class="brand-dot"></span><span class="brand-name">Velmora Gems</span></div>
    <div class="abs account-links">MY ACCOUNT &nbsp; | &nbsp; LOGIN</div>
    <div class="abs search"><div class="search-input">Enter search items</div><div class="search-btn">SEARCH</div></div>
    <div class="abs cart">YOUR CART IS &nbsp;<b>0 ITEMS</b></div>
  </header>

  <nav class="abs nav">
    <a style="left:33px">HOME</a>
    <a style="left:115px">ABOUT US</a>
    <a style="left:213px">CATALOGUE</a>
    <a style="left:317px">PRODUCTS</a>
    <a style="left:417px">ONLINE SHOPPING</a>
    <a style="left:546px">LOCATION</a>
    <a style="left:642px">CONTACT US</a>
  </nav>

  <section class="abs hero">
    <div class="hero-art" role="img" aria-label="Two platinum diamond engagement rings with princess and emerald cut stones"></div>
    <div class="hero-title">The<br>Custom Cart</div>
    <div class="hero-offer">20% off</div>
    <div class="hero-sub">Discount applied in cart</div>
    <div class="hero-btn">Order Now</div>
    <div class="hero-dots"><span></span><span></span><span></span><span></span></div>
  </section>

  <section class="abs welcome">
    <h1>WELCOME TO VELMORA GEMS</h1>
    <p>It is a long established fact that a reader will be distracted by the readable content of a page when looking at its layout. The point of using Lorem Ipsum<br>is that it has a more-or-less normal distribution of letters, as opposed to using 'Content here, content here.</p>
  </section>

  <section class="abs tile tile-bracelets">
    <div class="tile-art" role="img" aria-label="Diamond set bracelet links" style="left:35px;top:22px;width:140px;height:100px;border-radius:12px;background:linear-gradient(135deg,#d9d9d9,#8d8d8d)"></div>
    <div class="cond l1">BRACELETS</div>
    <div class="cond l2">GET EXCLUSIVE DISCOUNT</div>
    <div class="cond l3">ON ALL COLLECTIONS</div>
  </section>

  <section class="abs tile tile-offer">
    <div class="cond l1">LOREM IPSUM IS</div>
    <div class="cond l2">40% OFFER</div>
    <div class="cond l3">FOR SPECIAL PRODUCTS</div>
    <div class="tile-art" role="img" aria-label="Diamond pavé ring with a princess cut centre stone" style="left:243px;top:14px;width:120px;height:110px;border-radius:14px;background:linear-gradient(135deg,#f2f2f2,#9a9a9a)"></div>
  </section>

  <section class="abs tile tile-stones">
    <div class="tile-art" role="img" aria-label="Loose round brilliant diamonds on dark cloth" style="left:0;top:0;width:210px;height:132px;background:radial-gradient(ellipse at 45% 55%,#9c9c9c 0%,#4a4a4a 45%,#050505 100%)"></div>
    <div class="l1">Stones for ring</div>
    <div class="l2">offer</div>
    <div class="l3">Buy Our Product</div>
    <div class="l4">20% off</div>
  </section>

  <section class="abs tile tile-dollars">
    <div class="l1">Dollers products</div>
    <div class="cond l2">LOREM IPSUM IS SIMPLY</div>
    <div class="rule" style="top:79px"></div>
    <div class="cond l3">TEXT OF THE PRINTING</div>
    <div class="rule" style="top:106px"></div>
    <div class="tile-art" role="img" aria-label="Silver spiral pendant set with diamonds" style="left:250px;top:10px;width:115px;height:110px;border-radius:50%;background:radial-gradient(circle,#fff 30%,#cfcfcf 60%,#fff 80%)"></div>
  </section>

  <section class="abs promise">
    <p>EXQUISITE CRAFTSMANSHIP FINEST QUALITY DIAMONDS"</p>
    <p>"WILL BEAT ANY COMPETITORS PRICE BY TWENTY TO SEVENTY PERCENT GUARANTEED"</p>
    <p>"PRICE QUOTES WITHIN 24 HOURS"</p>
  </section>

  <footer class="abs footer">
    <ul class="footer-links">
      <li>Home</li><li>About Us</li><li>Catalogue</li><li>Products</li><li>Online Shopping</li><li>Location</li><li>Contact Us</li>
    </ul>
    <div class="enquiry-title">Engagement Ring</div>
    <div class="field" style="left:165px;top:49px">Name :</div>
    <div class="field" style="left:320px;top:49px">Email :</div>
    <div class="field" style="left:165px;top:78px">Phone :</div>
    <div class="field" style="left:320px;top:78px">Competitor Link :</div>
    <div class="field" style="left:165px;top:106px">Budget :</div>
    <div class="submit">SUBMIT</div>
    <div class="badge">
      <div class="badge-band"></div>
      <div class="badge-globe" role="img" aria-label="Golden globe emblem"></div>
      <div class="badge-title">Custom Jewellery</div>
      <div class="badge-sub">Create your own jewellery</div>
    </div>
    <div class="follow">FOLLOW US :</div>
    <div class="social" style="left:674px;background:#2b63b5"></div>
    <div class="social" style="left:703px;background:#2ba4d8"></div>
    <div class="social" style="left:732px;background:#1b7ea3"></div>
  </footer>

  <div class="abs copyright">Copyright © 2013. Velmora Gems. All Rights Reserved</div>
</div>
</body>
</html>
```